Varnik Holdings — Business Card Design Brief
Overview
Design a double-sided business card for Varnik Holdings that highlights our two service arms: Varnik Communications (telecommunications) and Varnik Energy (business energy solutions). The card should feel smart and stand out when handed to clients.

Objectives
Showcase our areas of specialty clearly.
Reflect the overall Varnik / Varnik Holdings brand while acknowledging both arms.
Explore using both logos (Communications + Energy) or one unified logo, depending on the design.

Deliverables
One double-sided business card design (front + back).

Content & Copy
Front (preferred): Logo: Varnik / Varnik Holdings
Descriptor: Business Communications | Business Energy
Back:My contact details and company details
Core products: Business Mobile • Telephony • Internet • Business Energy Solutions

Brand & Visual Direction
We have a group logo currently tailored more toward telecoms, plus a separate Varnik Energy logo.
Please explore layouts that use both logos or just one, whichever works best.
Color: I wouldn't mind seeing an option using our the Blue/Purple gradient from our website (varnik-example.co.uk), but also open to non-gradient approaches and other colours..

Overall look: Smart, modern, and distinctive.
Format & Print Specs
Double-sided business card format. (Use a standard size

Must-Haves
Front: Varnik wording or Varnik Holdings wording with atleast 1 logo also on front “Business Communications | Business Energy.”

Back: Contact + company details and core products.
A design that stands out while remaining professional.

Nice-to-Have Options
A gradient version using our site’s Blue/Purple gradient.
A non-gradient version.
A dual-logo treatment versus a single-logo treatment.

Thanks
Owen

```html
<!DOCTYPE html>
<html lang="en">
<head>
<meta charset="utf-8">
<title>Varnik Holdings — Business Card</title>
<link rel="stylesheet" href="https://fonts.googleapis.com/css2?family=Poppins:wght@400;500;700;800&display=swap">
<style>
  :root{
    --bg:#2a2a2c;
    --card:#1d1d1e;
    --navy:#25267a;
    --green:#3cb44a;
    --lime:#c9d82b;
    --yellow:#e4e01f;
    --blue:#2f6fc4;
    --purple:#8b3fa6;
    --white:#f4f4f4;
  }
  *{margin:0;padding:0;box-sizing:border-box}
  html,body{width:1200px;height:800px;overflow:hidden}
  body{background:var(--bg);font-family:"Poppins",sans-serif;color:var(--white);position:relative}
  .card{position:absolute;top:235px;width:540px;height:330px;background:var(--card);border-radius:26px;overflow:hidden;box-shadow:0 18px 40px rgba(0,0,0,.45)}
  .card--front{left:30px;border-bottom:3px solid var(--green);border-left:3px solid var(--green)}
  .card--back{left:630px;border-bottom:3px solid var(--green);border-left:3px solid var(--green)}

  .brand{display:flex;align-items:center;gap:12px}
  .brand__dot{width:46px;height:46px;border-radius:50%;border:7px solid var(--green)}
  .brand__name{font-weight:800;font-size:54px;color:var(--navy);letter-spacing:1px;line-height:1}

  .card--front .brand{position:absolute;left:50%;top:92px;transform:translateX(-50%)}
  .descriptor{position:absolute;left:0;right:0;top:205px;text-align:center;font-size:15px;font-weight:400;letter-spacing:.3px}

  .card--back .brand{position:absolute;right:34px;top:30px;gap:10px}
  .card--back .brand__dot{border-color:var(--blue);width:32px;height:32px;border-width:5px}
  .card--back .brand__name{font-size:36px}

  .person{position:absolute;left:28px;top:78px;padding-left:16px}
  .person__bar{position:absolute;left:0;top:4px;width:7px;height:48px;background:linear-gradient(var(--yellow),var(--lime))}
  .person__name{font-weight:700;font-size:26px;color:var(--green);line-height:1.1}
  .person__role{font-size:14px;font-weight:500}

  .address{position:absolute;left:44px;top:160px;font-size:13.5px;line-height:1.45}
  .contacts{position:absolute;left:44px;top:212px;list-style:none;font-size:13.5px;line-height:1.55}
  .contacts li{display:flex;align-items:center;gap:8px}
  .contacts svg{width:13px;height:13px;flex:none}

  .products{position:absolute;right:34px;top:118px;list-style:none;font-size:13.5px;line-height:1.6}
  .products li{display:flex;align-items:center;gap:8px}
  .products li::before{content:"";width:7px;height:7px;border-radius:50%;background:var(--lime)}

  .bands{position:absolute;right:0;bottom:0;width:540px;height:330px}
</style>
</head>
<body>

<section class="card card--front" aria-label="Card front">
  <div class="brand">
    <span class="brand__dot"></span>
    <span class="brand__name">VARNIK</span>
  </div>
  <p class="descriptor">Business Communications | Business Energy</p>
</section>

<section class="card card--back" aria-label="Card back">
  <svg class="bands" viewBox="0 0 540 330" aria-hidden="true">
    <defs>
      <linearGradient id="strip" x1="0" y1="1" x2="1" y2="0">
        <stop offset="0" stop-color="#8b3fa6"/>
        <stop offset=".5" stop-color="#2f6fc4"/>
        <stop offset="1" stop-color="#23307a"/>
      </linearGradient>
      <linearGradient id="corner" x1="0" y1="1" x2="1" y2="0">
        <stop offset="0" stop-color="#3cb44a"/>
        <stop offset="1" stop-color="#e4e01f"/>
      </linearGradient>
    </defs>
    <polygon points="300,330 540,235 540,262 345,330" fill="url(#strip)"/>
    <line x1="290" y1="330" x2="510" y2="235" stroke="#c9d82b" stroke-width="3"/>
    <polygon points="470,248 540,200 540,240" fill="url(#corner)"/>
  </svg>

  <div class="brand">
    <span class="brand__dot"></span>
    <span class="brand__name">VARNIK</span>
  </div>

  <div class="person">
    <span class="person__bar"></span>
    <h1 class="person__name">Mira Dolanska</h1>
    <p class="person__role">Founder &amp; CEO</p>
  </div>

  <p class="address">24 Alder Row, Leeds,<br>England, LS2 7QX</p>

  <ul class="contacts">
    <li><svg viewBox="0 0 24 24"><path fill="#c9d82b" d="M6.6 10.8a15 15 0 0 0 6.6 6.6l2.2-2.2a1 1 0 0 1 1-.25 11 11 0 0 0 3.6.6 1 1 0 0 1 1 1V20a1 1 0 0 1-1 1A17 17 0 0 1 3 4a1 1 0 0 1 1-1h3.5a1 1 0 0 1 1 1 11 11 0 0 0 .6 3.6 1 1 0 0 1-.25 1z"/></svg>+44 0113 496 0721</li>
    <li><svg viewBox="0 0 24 24"><circle cx="12" cy="12" r="9" fill="none" stroke="#3cb44a" stroke-width="2.5"/><path d="M3 12h18M12 3c3 3 3 15 0 18M12 3c-3 3-3 15 0 18" fill="none" stroke="#3cb44a" stroke-width="1.8"/></svg>www.varnik-example.co.uk</li>
    <li><svg viewBox="0 0 24 24"><rect x="2" y="5" width="20" height="14" rx="2" fill="#c9d82b"/><path d="M2 6l10 7 10-7" fill="none" stroke="#1d1d1e" stroke-width="2"/></svg>info@varnik-example.co.uk</li>
  </ul>

  <ul class="products">
    <li>Business Mobile</li>
    <li>Telephony</li>
    <li>Internet</li>
    <li>Business Energy Solutions</li>
  </ul>
</section>

</body>
</html>
```